"Tovi's" Website Design

Tovi's makes earth friendly, healthy, and delicious snacks that are completely gluten free. We are looking for a website that is easy to navigate, energetic, and conveys our purpose "To create healthy, earth-friendly, gluten free snacks that fill bellies and warm hearts."
Our first product is "Tovi's Crunch Rockets" are a small, square, cracker pack with an unreasonable amount of cheddar cheese flavor. The flavor literally explodes in your mouth!
We really want our site to pop and show off some personality.
I'm attaching the logo for the company, feel free to go beyond the logo in terms of color.
Here are some sites that we like!
http://www.plumvaleco.com/company
http://www.mirtlefarm.com/
http://www.qv47.com/
http://www.dexterwalts.com/
http://www.hovrapack.com/food/products_zing/
http://www.perrinsfrostery.com/

```html
<!DOCTYPE html>
<html lang="en">
<head>
<meta charset="utf-8">
<title>Tovi's</title>
<link rel="stylesheet" href="https://fonts.googleapis.com/css2?family=Kalam:wght@300;400;700&family=PT+Sans:wght@400&display=swap">
<style>
:root{
  --orange:#ff5e1f;
  --orange-dark:#d4420c;
  --grey-band:#e6e7e8;
  --ink:#1f1f1f;
  --line:#e4d6cf;
  --white:#ffffff;
  --hand:'Kalam', cursive;
  --body:'PT Sans', sans-serif;
}
*{margin:0;padding:0;box-sizing:border-box}
html,body{width:1200px;height:1067px;overflow:hidden;background:var(--white)}
.page{position:relative;width:1200px;height:1067px;font-family:var(--body)}
.abs{position:absolute}
h2,h3{font-weight:400}

.header-band{left:0;top:0;width:1200px;height:134px;background:var(--grey-band);border-top:2px solid var(--orange)}
.brand{left:155px;top:16px;font-family:var(--hand);font-weight:700;font-size:56px;color:var(--orange);letter-spacing:2px}
.main-nav{left:434px;top:0;width:597px;height:38px;background:var(--orange);display:flex;justify-content:space-around;align-items:center;box-shadow:0 6px 6px -3px rgba(0,0,0,.45)}
.main-nav a{font-family:var(--hand);font-size:15px;color:var(--white);text-decoration:none;font-style:italic}
.search{left:851px;top:66px;width:178px;height:25px;background:var(--white);border:1px solid #c9c9c9;font-family:var(--hand);font-size:14px;color:var(--orange);padding:1px 9px;font-style:italic}
.search svg{position:absolute;right:6px;top:4px}

.slider{left:152px;top:118px;width:895px;height:290px;background:var(--white);border:1px solid #e0e0e0}
.slider-sheen{left:4px;top:4px;width:885px;height:60px;background:linear-gradient(#e9e9e9,#fff)}
.slide-photo{left:19px;top:30px;width:443px;height:180px;border-radius:40% 45% 30% 30%;background:radial-gradient(ellipse at 50% 50%,#f7932f 0%,#f58a24 55%,#fbd3a8 85%,#fff 100%)}
.slide-heading{left:508px;top:46px;font-family:var(--hand);font-size:28px;color:var(--orange);font-style:italic}
.slide-text{left:508px;top:88px;width:350px;font-family:var(--hand);font-size:19px;line-height:23px;color:var(--ink);font-style:italic}
.pager{left:683px;top:231px;display:flex;gap:5px}
.pager span{width:25px;height:25px;border:1px solid #d9d9d9;font-family:var(--hand);font-size:16px;color:var(--orange);text-align:center;line-height:24px;font-style:italic}

.band{left:0;top:399px;width:1200px;height:374px;background:var(--orange)}
.product-pack{left:150px;top:444px;width:110px;height:153px;border-radius:6px;background:linear-gradient(#efe6d6 0%,#e8833a 45%,#d9661f 75%,#ece3d4 100%);box-shadow:3px 4px 8px rgba(0,0,0,.35)}
.section-title{font-family:var(--hand);font-size:21px;color:var(--ink);font-style:italic;border-bottom:1px dotted var(--ink);padding-bottom:2px}
.section-text{font-size:10.5px;line-height:18.5px;color:var(--white)}
.products-title{left:286px;top:452px;width:277px}
.products-text{left:286px;top:503px;width:310px}
.divider{left:631px;top:437px;height:176px;border-left:1px dotted var(--ink)}
.welcome-title{left:657px;top:452px;width:390px}
.welcome-text{left:657px;top:499px;width:385px}

.panel{left:149px;top:649px;width:896px;height:311px;background:var(--white);box-shadow:2px 3px 4px rgba(0,0,0,.25);clip-path:polygon(30px 0,866px 0,896px 26px,896px 100%,0 100%,0 26px)}
.tab{top:649px;height:36px;background:var(--orange-dark);font-family:var(--hand);font-size:21px;color:var(--white);text-align:center;line-height:38px;font-style:italic;border-radius:0 0 4px 4px}
.tab-chips{left:182px;width:173px;clip-path:polygon(0 0,100% 0,96% 100%,4% 100%)}
.tab-services{left:834px;width:176px;clip-path:polygon(0 0,100% 0,97% 100%,3% 100%)}

.carousel{left:161px;top:715px;width:473px;height:115px;border:1px solid var(--line)}
.carousel .arrow{position:absolute;top:48px}
.chip-bag{position:absolute;top:9px;width:62px;height:92px;border-radius:4px}
.bag-1{left:49px;background:linear-gradient(#d9742f,#b9521f)}
.bag-2{left:152px;background:linear-gradient(#c8372b,#e0a25a)}
.bag-3{left:257px;background:linear-gradient(#a9c7e0,#d7c7a2)}
.bag-4{left:357px;background:linear-gradient(#6aa2d6,#2f6fb0)}

.newsletter-title{left:163px;top:843px;font-family:var(--hand);font-size:19px;color:var(--orange);font-style:italic}
.field{top:882px;width:183px;height:26px;border:1px solid #cfcfcf;font-family:var(--hand);font-size:13px;color:#444;padding:3px 8px;font-style:italic}
.field-name{left:164px}
.field-email{left:356px}
.signup{left:549px;top:882px;width:76px;height:26px;background:var(--orange);border:1px solid #e7a283;font-family:var(--hand);font-size:17px;color:var(--white);text-align:center;line-height:25px;font-style:italic}

.services-box{left:649px;top:713px;width:386px;height:174px;border:1px solid var(--line)}
.services-photo{left:661px;top:724px;width:125px;height:151px;background:linear-gradient(135deg,#e59a2e,#f2b04a 50%,#d7751d)}
.services-text{left:799px;top:721px;width:228px;font-size:10.5px;line-height:18.5px;color:#333}
.more{left:801px;top:839px;font-family:var(--hand);font-size:17px;color:var(--orange);font-style:italic}

.footer-nav{left:0;top:990px;width:1148px;text-align:center;font-family:var(--hand);font-size:13px;color:var(--ink);font-style:italic;word-spacing:2px}
.footer-nav span{margin:0 17px}
.copyright{left:0;top:1014px;width:1148px;text-align:center;font-family:var(--hand);font-size:13px;color:var(--ink);font-style:italic}
</style>
</head>
<body>
<div class="page">
  <div class="abs header-band"></div>
  <div class="abs brand">Tovi's</div>
  <nav class="abs main-nav">
    <a href="#">Home</a><a href="#">Company</a><a href="#">Our Products</a><a href="#">Services</a><a href="#">News</a><a href="#">Contact us</a>
  </nav>
  <div class="abs search">search
    <svg width="14" height="15" viewBox="0 0 14 15"><circle cx="5" cy="5" r="3.6" fill="none" stroke="#222" stroke-width="1.6"/><line x1="7.6" y1="7.8" x2="12.5" y2="13.5" stroke="#222" stroke-width="2.4"/></svg>
  </div>

  <section class="abs slider">
    <div class="abs slider-sheen"></div>
    <div class="abs slide-photo" role="img" aria-label="Pile of orange cheese puff snacks"></div>
    <h2 class="abs slide-heading">Heading</h2>
    <p class="abs slide-text">Lorem Ipsum is simply dummy text of the printing and typesetting industry.</p>
    <div class="abs pager"><span>1</span><span>2</span><span>3</span><span>4</span><span>5</span></div>
  </section>

  <div class="abs band"></div>

  <div class="abs product-pack" role="img" aria-label="Bag of baked cheese snacks"></div>
  <h3 class="abs section-title products-title">our products</h3>
  <p class="abs section-text products-text">Lorem Ipsum is simply dummy text of the printing and typeset-ting industry. Lorem Ipsum has been the industry's standard dummy text ever since the 1500s,when an unknown printer took a galley of type and scrambled it to make a type</p>
  <div class="abs divider"></div>
  <h3 class="abs section-title welcome-title">welcome to our site</h3>
  <p class="abs section-text welcome-text">Lorem Ipsum is simply dummy text of the printing and typesetting industry. Lorem Ipsum has been the industry's standard dummy text ever since the 1500s,when an unknown printer took a galley of type and scrambled it to make a type specimen book. It has survived not only five centuries, but also the leap into electronic type-setting, remaining essentially unchanged. It was popularised in the 1960s with the release of Letraset sheets containing Lorem Ipsum passages.</p>

  <div class="abs panel"></div>
  <div class="abs tab tab-chips">Our Chips</div>
  <div class="abs tab tab-services">Services</div>

  <div class="abs carousel">
    <svg class="arrow" style="left:14px" width="10" height="16" viewBox="0 0 10 16"><polyline points="8,2 2,8 8,14" fill="none" stroke="#222" stroke-width="2.5"/></svg>
    <div class="chip-bag bag-1" role="img" aria-label="Bag of potato chips"></div>
    <div class="chip-bag bag-2" role="img" aria-label="Bag of potato chips"></div>
    <div class="chip-bag bag-3" role="img" aria-label="Bag of potato chips"></div>
    <div class="chip-bag bag-4" role="img" aria-label="Bag of potato chips"></div>
    <svg class="arrow" style="left:450px" width="10" height="16" viewBox="0 0 10 16"><polyline points="2,2 8,8 2,14" fill="none" stroke="#222" stroke-width="2.5"/></svg>
  </div>

  <h3 class="abs newsletter-title">newsletter signup</h3>
  <div class="abs field field-name">enter your name</div>
  <div class="abs field field-email">enter your &nbsp;e mail id</div>
  <div class="abs signup">Sign up</div>

  <div class="abs services-box"></div>
  <div class="abs services-photo" role="img" aria-label="Hand picking up square cheese crackers"></div>
  <p class="abs services-text">Lorem Ipsum is simply dummy text of the print-ing and typesetting industry. Lorem Ipsum has been the industry's standard dummy text ever since the 1500s,when an unknown printer took a galley of type and scrambled it to make a type specimen book.</p>
  <div class="abs more">more +</div>

  <nav class="abs footer-nav">Home<span>/</span>Company<span>/</span>Our Products<span>/</span>Services<span>/</span>News<span>/</span>Contact us</nav>
  <div class="abs copyright">Copyrights &nbsp;@ 2012 All Rights Reserved</div>
</div>
</body>
</html>
```